Unique Business Card Design

Unique Business Card design for our orthotic and prosthetic company. Our logo is on our website, color is light blue. Unique shape (artificial leg shaped, vertical, etc..) preferred. Logo, business name, individual name and basic demographics needed.

Industry/Entity Type

Business

Contact Information for Business Card

Logo, Industry, Phone # Logo, "Prosthetic & Orthotic Services" Place to add individual name and contact info

Colors
cee9f5

Requirements
Must have
• The icon must be there, placement of "Prosthetic & Orthotic Services" can be moved
Nice to have
• Like the mix of light blue, and a little darker blue. One design included the icons from my website which was a nice touch

```html
<!DOCTYPE html>
<html lang="en">
<head>
<meta charset="utf-8">
<title>Limbwell Inc. Business Card</title>
<link rel="stylesheet" href="https://fonts.googleapis.com/css2?family=Open+Sans:wght@400;600;700&display=swap">
<style>
  :root {
    --brand-blue: #1560ad;
    --ink: #4a4a4a;
    --paper: #ffffff;
    --backdrop: #3f3f41;
    --rule-grey: #9a9a9a;
    --divider: #d4d4d4;
  }
  * { box-sizing: border-box; margin: 0; padding: 0; }
  html, body {
    width: 1105px; height: 1200px; overflow: hidden;
    background: var(--backdrop);
    font-family: "Open Sans", Arial, sans-serif;
  }
  .sheet { position: relative; width: 1105px; height: 1200px; }
  .card {
    position: absolute; left: 192px; width: 720px; height: 412px;
    overflow: hidden;
  }
  .card--front { top: 166px; background: var(--paper); }
  .card--back { top: 610px; background: var(--brand-blue); }

  /* Brand lockup */
  .brand { position: absolute; display: flex; align-items: center; }
  .brand__dot { border-radius: 50%; flex: none; }
  .brand__text { display: flex; flex-direction: column; }
  .brand__name { font-weight: 600; white-space: nowrap; letter-spacing: -0.2px; }
  .brand__tagline { font-weight: 400; white-space: nowrap; }

  .card--front .brand { left: 41px; top: 166px; }
  .card--front .brand__dot { width: 80px; height: 80px; background: var(--brand-blue); margin-right: 17px; }
  .card--front .brand__name { font-size: 24px; color: var(--brand-blue); line-height: 1.1; }
  .card--front .brand__tagline { font-size: 11.5px; color: var(--brand-blue); margin-top: 4px; }

  .card--back .brand { left: 137px; top: 148px; }
  .card--back .brand__dot { width: 118px; height: 118px; background: var(--paper); margin-right: 28px; }
  .card--back .brand__name { font-size: 34px; color: var(--paper); line-height: 1.1; }
  .card--back .brand__tagline { font-size: 16px; color: var(--paper); margin-top: 6px; }

  .divider {
    position: absolute; left: 363px; top: 66px; width: 1px; height: 280px;
    background: var(--divider);
  }

  .contact { position: absolute; left: 392px; top: 76px; color: var(--ink); }
  .contact__name { font-size: 25px; font-weight: 700; color: var(--brand-blue); letter-spacing: 0.3px; line-height: 1.1; }
  .contact__title { font-size: 16px; font-weight: 600; color: var(--brand-blue); margin-top: 4px; }
  .contact__address { font-size: 18.5px; line-height: 27px; margin-top: 12px; }
  .contact__list { list-style: none; margin-top: 6px; }
  .contact__item { display: flex; align-items: center; font-size: 18.5px; line-height: 27.5px; }
  .contact__icon { width: 18px; height: 18px; margin-right: 11px; fill: var(--brand-blue); flex: none; }

  .footer-rule { position: absolute; left: 0; top: 378px; width: 100%; height: 2px; background: var(--rule-grey); }
  .footer-band { position: absolute; left: 0; top: 382px; width: 100%; height: 30px; background: var(--brand-blue); }
</style>
</head>
<body>
<main class="sheet">

  <section class="card card--front" aria-label="Business card front">
    <div class="brand">
      <span class="brand__dot"></span>
      <div class="brand__text">
        <span class="brand__name">LIMBWELL INC.</span>
        <span class="brand__tagline">Prosthetic &amp; Orthotic Services</span>
      </div>
    </div>

    <div class="divider"></div>

    <div class="contact">
      <p class="contact__name">MIRIAM SOLBERG</p>
      <p class="contact__title">CO LPO</p>
      <p class="contact__address">2350 W. 14th St.<br>Brooklyn, NY 11223</p>
      <ul class="contact__list">
        <li class="contact__item">
          <svg class="contact__icon" viewBox="0 0 24 24" aria-hidden="true"><path d="M6.6 10.8c1.4 2.8 3.8 5.1 6.6 6.6l2.2-2.2c.3-.3.7-.4 1-.2 1.1.4 2.3.6 3.6.6.6 0 1 .4 1 1V20c0 .6-.4 1-1 1C10.6 21 3 13.4 3 4c0-.6.4-1 1-1h3.5c.6 0 1 .4 1 1 0 1.3.2 2.5.6 3.6.1.3 0 .7-.2 1L6.6 10.8z"/></svg>
          555.210.4400
        </li>
        <li class="contact__item">
          <svg class="contact__icon" viewBox="0 0 24 24" aria-hidden="true"><path d="M7 1h10c1.1 0 2 .9 2 2v18c0 1.1-.9 2-2 2H7c-1.1 0-2-.9-2-2V3c0-1.1.9-2 2-2zm0 3v14h10V4H7zm5 15.5a1.2 1.2 0 1 0 0 2.4 1.2 1.2 0 0 0 0-2.4z"/></svg>
          555.210.4417
        </li>
        <li class="contact__item">
          <svg class="contact__icon" viewBox="0 0 24 24" aria-hidden="true"><path d="M7 2h10v5H7zM4 8h16c1.1 0 2 .9 2 2v7h-4v5H6v-5H2v-7c0-1.1.9-2 2-2zm4 7v5h8v-5H8z"/></svg>
          555-3086142
        </li>
        <li class="contact__item">
          <svg class="contact__icon" viewBox="0 0 24 24" aria-hidden="true"><path d="M2 5h20v14H2V5zm2 2v.5l8 5 8-5V7H4zm0 2.8V17h16V9.8l-8 5-8-5z"/></svg>
          Msolberg@limbwellinc.com
        </li>
        <li class="contact__item">
          <svg class="contact__icon" viewBox="0 0 24 24" aria-hidden="true"><path d="M12 2a10 10 0 1 0 0 20 10 10 0 0 0 0-20zm-1 17.9A8 8 0 0 1 4.1 10.6L9 15.5v1c0 1.1.9 2 2 2v1.4zm6.9-2.5c-.3-.8-1-1.4-1.9-1.4h-1v-3c0-.6-.4-1-1-1H8v-2h2c.6 0 1-.4 1-1V6h2c1.1 0 2-.9 2-2v-.4a8 8 0 0 1 2.9 13.8z"/></svg>
          www.limbwellinc.com
        </li>
      </ul>
    </div>

    <div class="footer-rule"></div>
    <div class="footer-band"></div>
  </section>

  <section class="card card--back" aria-label="Business card back">
    <div class="brand">
      <span class="brand__dot"></span>
      <div class="brand__text">
        <span class="brand__name">LIMBWELL INC.</span>
        <span class="brand__tagline">Prosthetic &amp; Orthotic Services</span>
      </div>
    </div>
  </section>

</main>
</body>
</html>
```